Structural Engineering Business Card

Brookvane Drafting does residential house plans for clients in Central Florida. Would like simple but elegant business card that is appropriate for a house plan engineering company. Prefer black business card with black/white them but open to other shades of blue. I uploaded a sample card that I came across that looked good but please come up with your own creative designs.

Contact Information for Business Card

Name, Title, Phone, Email, Address, website

```html
<!DOCTYPE html>
<html lang="en">
<head>
<meta charset="utf-8">
<title>Brookvane Drafting – Business Card</title>
<link href="https://fonts.googleapis.com/css2?family=Roboto:wght@400;700;900&display=swap" rel="stylesheet">
<style>
  :root {
    --page-bg: #2a2a2a;
    --card-bg: #1c1c1d;
    --text-main: #ffffff;
    --text-soft: #e6e6e6;
    --mark-grey: #5c5c5e;
    --mark-dark: #0e0e0f;
  }
  * { margin: 0; padding: 0; box-sizing: border-box; }
  html, body {
    width: 1200px; height: 900px; overflow: hidden;
    background: var(--page-bg);
    font-family: "Roboto", Arial, sans-serif;
  }
  .sheet {
    width: 1200px; height: 900px;
    display: flex; flex-direction: column;
    align-items: center; justify-content: center; gap: 40px;
  }
  .card {
    position: relative;
    width: 640px; height: 366px;
    background: var(--card-bg);
    box-shadow: 0 10px 30px rgba(0,0,0,.45);
    overflow: hidden;
  }
  /* Front */
  .card-front .person { position: absolute; left: 44px; top: 40px; }
  .person-name {
    color: var(--text-main); font-weight: 900; font-size: 26px;
    letter-spacing: .5px; text-transform: uppercase; line-height: 1;
  }
  .person-title { color: var(--text-soft); font-size: 17px; margin-top: 4px; }
  .address {
    position: absolute; left: 44px; top: 150px;
    color: var(--text-soft); font-size: 16px; line-height: 1.35;
  }
  .contact-list {
    position: absolute; left: 44px; top: 214px;
    list-style: none; color: var(--text-soft); font-size: 16px; line-height: 1.55;
  }
  .contact-list li { display: flex; align-items: center; gap: 8px; }
  .contact-list svg { width: 14px; height: 14px; fill: var(--text-soft); flex: none; }
  .front-brand {
    position: absolute; right: 40px; bottom: 44px; text-align: right;
    color: var(--mark-grey); font-weight: 900; font-size: 30px;
    line-height: 1.05; text-transform: uppercase;
  }
  /* Back */
  .card-back { display: flex; align-items: center; justify-content: center; gap: 22px; }
  .back-square { width: 56px; height: 56px; background: var(--mark-dark); flex: none; }
  .back-brand {
    color: var(--mark-grey); font-weight: 900; font-size: 52px;
    line-height: 1; text-transform: uppercase;
  }
</style>
</head>
<body>
<main class="sheet">
  <section class="card card-front" aria-label="Business card front">
    <div class="person">
      <p class="person-name">Daniel Reyes</p>
      <p class="person-title">Founder/CEO</p>
    </div>
    <p class="address">2290 Harbor Row Suite 140<br>Lakewood, FL 32801</p>
    <ul class="contact-list">
      <li>
        <svg viewBox="0 0 16 16" aria-hidden="true"><path d="M3 2h3l1.2 3.2-1.8 1.3a9 9 0 0 0 4.1 4.1l1.3-1.8L14 10v3a1 1 0 0 1-1 1A11 11 0 0 1 2 3a1 1 0 0 1 1-1z"/></svg>
        407.555.0182
      </li>
      <li>
        <svg viewBox="0 0 16 16" aria-hidden="true"><path d="M1 3h14v10H1z M1.5 3.5 8 9l6.5-5.5" fill="none" stroke="#e6e6e6" stroke-width="1.4"/></svg>
        info@brookvanedrafting.com
      </li>
      <li>
        <svg viewBox="0 0 16 16" aria-hidden="true"><circle cx="8" cy="8" r="6.3" fill="none" stroke="#e6e6e6" stroke-width="1.3"/><path d="M1.7 8h12.6M8 1.7c-3 3.5-3 9.1 0 12.6M8 1.7c3 3.5 3 9.1 0 12.6" fill="none" stroke="#e6e6e6" stroke-width="1.1"/></svg>
        www.brookvanedrafting.com
      </li>
    </ul>
    <p class="front-brand">Brookvane<br>Drafting</p>
  </section>

  <section class="card card-back" aria-label="Business card back">
    <div class="back-square" aria-hidden="true"></div>
    <p class="back-brand">Brookvane<br>Drafting</p>
  </section>
</main>
</body>
</html>
```